Business card for a Exhibition booth fabrication company

Hi. My company would like to change our corporate name card. We are an events and Exhibition stand builder company. We would like our corporate name card to resonate what we do. I need someone to create something unique that relates to the industry that I am in. The graphic designer should be creative to incorporate the elements of my industry and try to blend in well in the design of the card. Our aim is to ensure that we are unique and our card can look different from our competitors.
Updates

Target Market(s)

Marketing and events manager from all companies

Contact Information for Business Card

The business card should have the following details:
Name
Job Title
Email
Website

Colors

Designer to choose colors to be used in the design.

Requirements
Must have
• The card must be look something that is relevant to the service that I am providing. My website is: www.velmora-buildworks.com
• You can see my website to get more information on what service that I am doing
Nice to have
• On the back of my card, I would like to have a globe image with the incorporation of my company logo. This is to indicate that my services can be done in any part of the world.

```html
<!DOCTYPE html>
<html lang="en">
<head>
<meta charset="utf-8">
<title>Velmora Buildworks – Business Card</title>
<link rel="stylesheet" href="https://fonts.googleapis.com/css2?family=Open+Sans:wght@400;600;700;800&display=swap">
<style>
  :root {
    --page-bg: #efefef;
    --card-bg: #ffffff;
    --brand-red: #e3202c;
    --text-grey: #4a4a4a;
    --brand-grey: #5a5a5a;
    --rose: #f2c3d3;
    --mauve: #e2cad3;
    --map-tone: #c4c4c4;
  }
  * { box-sizing: border-box; margin: 0; padding: 0; }
  html, body {
    width: 1200px; height: 864px; overflow: hidden;
    background: var(--page-bg);
    font-family: "Open Sans", Arial, sans-serif;
  }
  .card {
    position: absolute;
    left: 285px;
    width: 630px; height: 360px;
    background: var(--card-bg);
    box-shadow: 0 6px 18px rgba(0,0,0,0.12);
    overflow: hidden;
  }
  .card--details { top: 40px; }
  .card--globe { top: 464px; }

  .card__shapes { position: absolute; inset: 0; }

  .brand {
    position: absolute;
    display: flex; align-items: center; gap: 8px;
    color: var(--brand-grey);
    font-weight: 600;
    letter-spacing: 0.16em;
    text-transform: uppercase;
    white-space: nowrap;
  }
  .brand__dot {
    width: 14px; height: 14px; border-radius: 50%;
    background: var(--brand-red);
  }
  .card--details .brand { left: 200px; top: 26px; font-size: 14px; }

  .contact {
    position: absolute; left: 34px; top: 214px;
    list-style: none;
    font-size: 17px; line-height: 1.55;
    color: var(--text-grey);
  }
  .contact__label { color: var(--brand-red); font-weight: 700; }

  .map {
    position: absolute; left: 80px; top: 30px;
    width: 500px; height: 230px;
    background: radial-gradient(ellipse 50% 50% at 55% 50%,
                rgba(180,180,180,0.75) 0%,
                rgba(200,200,200,0.5) 45%,
                rgba(230,230,230,0.2) 75%,
                rgba(255,255,255,0) 100%);
  }

  .card--globe .brand {
    left: 50%; top: 244px; transform: translateX(-50%);
    font-size: 14px;
  }
  .tagline {
    position: absolute; left: 0; right: 0; top: 290px;
    text-align: center;
    color: var(--brand-red);
    font-weight: 800;
    font-size: 31px;
    letter-spacing: 0.02em;
  }
</style>
</head>
<body>

  <section class="card card--details">
    <svg class="card__shapes" viewBox="0 0 630 360" aria-hidden="true">
      <polygon points="300,70 540,70 630,130 630,245 440,245 330,150" fill="var(--mauve)"/>
      <polygon points="440,265 630,265 630,360 300,360" fill="var(--mauve)"/>
      <polygon points="205,160 300,95 375,210 300,360 215,360 150,300" fill="var(--rose)"/>
    </svg>
    <div class="brand"><span class="brand__dot"></span>Velmora Buildworks</div>
    <ul class="contact">
      <li><span class="contact__label">Name:</span> Daniel Harlow</li>
      <li><span class="contact__label">Job Title:</span> Senior Consultant</li>
      <li><span class="contact__label">Email:</span> info@velmora-buildworks.com</li>
    </ul>
  </section>

  <section class="card card--globe">
    <div class="map" role="img" aria-label="Grey world map with dotted red routes reaching destinations around the globe"></div>
    <div class="brand"><span class="brand__dot"></span>Velmora Buildworks</div>
    <p class="tagline">Consult · Concept · Construct</p>
  </section>

</body>
</html>
```